Brindlewick Solutions Ltd

I'd like to create a company letterhead for the attached logo in word format.

I'd like to emphasis the icon in large translucent state from the left corner and ensure that the letterhead colouring matches the colour palette of the current logo with a contrast so it's clear to see. I've attached a copy of our sister company page on the app for reference.

```html
<!DOCTYPE html>
<html lang="en">
<head>
<meta charset="utf-8">
<title>Brindlewick Solutions Ltd — Letterhead</title>
<link rel="stylesheet" href="https://fonts.googleapis.com/css2?family=Roboto:wght@400&display=swap">
<style>
  :root {
    --backdrop: #dcdcdc;
    --paper: #f7f7f7;
    --brand-teal: #14b39e;
    --brand-tint: #e6f2f1;
    --ink-grey: #6d7172;
  }
  * { margin: 0; padding: 0; box-sizing: border-box; }
  html, body {
    width: 1153px;
    height: 1200px;
    overflow: hidden;
    background: var(--backdrop);
    font-family: "Roboto", Arial, sans-serif;
  }
  .letterhead {
    position: absolute;
    left: 168px;
    top: 30px;
    width: 817px;
    height: 1140px;
    overflow: hidden;
    background: var(--paper);
    box-shadow: 0 6px 18px rgba(0, 0, 0, 0.12);
  }
  .brand-watermark {
    position: absolute;
    left: 0;
    top: 0;
    width: 817px;
    height: 1140px;
  }
  .brand-watermark circle { fill: var(--brand-tint); }
  .brand {
    position: absolute;
    left: 73px;
    top: 66px;
    display: flex;
    align-items: center;
    gap: 12px;
  }
  .brand-dot {
    width: 34px;
    height: 34px;
    border-radius: 50%;
    background: var(--brand-teal);
  }
  .brand-name {
    font-size: 30px;
    font-weight: 400;
    color: var(--brand-teal);
    letter-spacing: 0.2px;
  }
  .contact-list {
    position: absolute;
    left: 73px;
    top: 1031px;
    list-style: none;
    font-size: 17px;
    line-height: 21px;
    color: var(--ink-grey);
  }
  .contact-item {
    display: flex;
    align-items: center;
    gap: 6px;
  }
  .contact-icon {
    width: 15px;
    height: 15px;
    fill: var(--brand-teal);
  }
  .postal-address {
    position: absolute;
    right: 76px;
    top: 1032px;
    font-style: normal;
    text-align: right;
    font-size: 17px;
    line-height: 21px;
    color: var(--ink-grey);
  }
</style>
</head>
<body>
  <main class="letterhead">
    <svg class="brand-watermark" viewBox="0 0 817 1140" role="img" aria-label="Large faint brand emblem watermark from the left edge">
      <circle cx="196" cy="598" r="400"/>
    </svg>

    <header class="brand">
      <span class="brand-dot" aria-hidden="true"></span>
      <span class="brand-name">Brindlewick Solutions Ltd</span>
    </header>

    <footer>
      <ul class="contact-list">
        <li class="contact-item">
          <svg class="contact-icon" viewBox="0 0 16 16" aria-hidden="true">
            <path d="M2 6c0-2 3-3 6-3s6 1 6 3v1h-3V5.5H5V7H2z"/>
            <path d="M4.5 8h7l1.5 5H3z"/>
            <circle cx="8" cy="10.5" r="1.3" fill="#f7f7f7"/>
          </svg>
          <span>1-888-555-0147</span>
        </li>
        <li class="contact-item">
          <svg class="contact-icon" viewBox="0 0 16 16" aria-hidden="true">
            <rect x="1" y="3.5" width="14" height="9" rx="0.5"/>
            <path d="M1.5 4l6.5 5 6.5-5" fill="none" stroke="#f7f7f7" stroke-width="1.2"/>
          </svg>
          <span>hello@brindlewick.co</span>
        </li>
        <li class="contact-item">
          <svg class="contact-icon" viewBox="0 0 16 16" aria-hidden="true">
            <circle cx="8" cy="8" r="7"/>
            <path d="M5 3.5c1.5 1 .5 2.5 2 3s1 2-.5 2.5-1 2.5 0 3.5M10 4c-.5 1.5.5 2 1.5 2.5s1 2 0 3" fill="none" stroke="#f7f7f7" stroke-width="1.1"/>
          </svg>
          <span>www.brindlewick.co</span>
        </li>
      </ul>

      <address class="postal-address">
        Brindlewick Solutions Ltd<br>
        48 W Meadowlark Ave Suite<br>
        7 Ashford, MS 38790
      </address>
    </footer>
  </main>
</body>
</html>
```